Responsive OnePage Design for recruitment company

BrightHire is a modern company that sources interim people for its customers. Mostly developers, scrum master, project managers and designers. In this website we want to tell something about us, about how we work, our customers and we want our candidates be able to subscribe. The subscription form should be several fields (name, surname, email address, phone number and the possibility to upload your resume.We want it to fit into a existing wordpress plugin. We also want a listing of our job opportunities. The listing should be designed in a clear readable overview and if you click on the job you should get the details and be able to respond quickly by filling in you name, surname, email address, rate, phone number and upload your resume. We want this to be a standard configurable plugin. It should be easy to fill in the jobs in Wordpress by our administrator. We want a fresh, modern and cool design. It should be a responsive onepage design. If you click on a listed job you should stay on the same page. Our logo is added.

Target Market(s)

recruitment

Industry/Entity Type

Recruitment

Font styles to use
Sans Serif

Colors

Designer to choose colors to be used in the design.

Requirements
Must have
• Onepage design
• listing of job opportunities
• subscription forms
• be responsive

```html
<!DOCTYPE html>
<html lang="en">
<head>
<meta charset="utf-8">
<title>BrightHire – Interim recruitment</title>
<link href="https://fonts.googleapis.com/css2?family=Poppins:wght@400;500;600;700&family=Open+Sans:wght@400;600&display=swap" rel="stylesheet">
<style>
:root{
  --blue:#1466c0;
  --blue-dark:#0d4f9c;
  --topbar:#1b5eaa;
  --ink:#1c1f26;
  --text:#5d6470;
  --muted:#8a919c;
  --line:#d9dde3;
  --grey-bg:#eeeff1;
  --sub-bg:#dfe4ee;
  --white:#ffffff;
  --orange:#f07a22;
}
*{box-sizing:border-box;margin:0;padding:0}
html,body{width:1200px;height:5085px;overflow:hidden}
body{font-family:"Open Sans",Arial,sans-serif;color:var(--text);background:var(--white);position:relative;font-size:14px}
h1,h2,h3,h4,.heading{font-family:"Poppins",Arial,sans-serif;color:var(--ink)}
section,header,footer,.topbar{position:absolute;left:0;width:1200px}
.wrap{position:absolute;left:142px;width:916px}

/* top bar */
.topbar{top:0;height:34px;background:var(--topbar);color:#fff;font-size:12px}
.topbar .contact{position:absolute;left:142px;top:9px;display:flex;gap:28px}
.topbar .contact span{display:flex;align-items:center;gap:6px}
.topbar .social{position:absolute;right:142px;top:8px;display:flex;gap:4px}
.dot{width:18px;height:18px;border-radius:50%;border:1px solid rgba(255,255,255,.8)}

/* header */
header{top:34px;height:96px;background:#fff;border-bottom:1px solid var(--line)}
.brand{position:absolute;left:142px;top:31px;font-family:"Poppins",Arial,sans-serif;font-weight:600;font-size:30px;letter-spacing:7px;color:var(--ink)}
nav{position:absolute;right:142px;top:40px;display:flex;gap:22px;font-family:"Poppins",Arial,sans-serif;font-size:13px;font-weight:500;color:var(--ink);text-transform:uppercase}

/* hero */
.hero{top:130px;height:565px}
.hero-photo{position:absolute;inset:0;background:linear-gradient(100deg,#f2f1ee 0%,#e7e2da 40%,#cfb48c 75%,#b99468 100%)}
.hero-title{position:absolute;left:142px;top:150px;font-family:"Poppins",Arial,sans-serif;font-size:46px;font-weight:500;letter-spacing:10px;color:var(--ink)}
.hero-text{position:absolute;left:142px;top:220px;width:470px;font-size:14.5px;line-height:24px;color:#3f4550}
.btn{display:inline-block;font-family:"Poppins",Arial,sans-serif;font-weight:600;text-transform:uppercase;font-size:13px}
.btn-solid{background:var(--blue);color:#fff;padding:13px 26px;border-radius:3px}
.hero .btn{position:absolute;left:142px;top:340px}
.arrow{position:absolute;width:34px;height:34px;border-radius:50%;background:#2a2d33;display:flex;align-items:center;justify-content:center}

/* welcome */
.welcome{top:695px;height:525px;background:var(--grey-bg)}
.welcome-photo{position:absolute;left:142px;top:78px;width:428px;height:352px;border:5px solid #fff;background:linear-gradient(160deg,#1a3f78,#2b78c4 55%,#0f2b57)}
.welcome-copy{position:absolute;left:623px;top:84px;width:430px}
.eyebrow{font-family:"Poppins",Arial,sans-serif;font-weight:600;font-size:15px;color:var(--ink);text-transform:uppercase}
.welcome-copy h2{font-size:38px;font-weight:600;letter-spacing:1px;color:var(--blue);line-height:48px}
.rule{width:50px;height:3px;background:var(--blue)}
.welcome-copy .rule{margin:12px 0 30px}
.welcome-copy p{font-size:14px;line-height:24px}
.btn-outline{border:2px solid var(--ink);color:var(--ink);padding:8px 22px;border-radius:20px;font-size:12px;margin-top:40px}

/* section title */
.section-title{position:absolute;left:0;width:1200px;text-align:center;font-size:38px;font-weight:700;text-transform:uppercase;color:var(--ink)}
.section-title span{font-weight:400;color:var(--blue)}
.section-rule{position:absolute;left:575px;width:50px;height:3px;background:var(--blue)}

/* how we work */
.how{top:1220px;height:610px}
.steps-line{position:absolute;left:268px;top:295px;width:657px;border-top:2px dotted #b5bcc7}
.step{position:absolute;top:230px;width:300px;text-align:center}
.step-icon{margin:0 auto;width:130px;height:130px;border-radius:50%;border:2px dashed #9fb6d4;background:#fff;display:flex;align-items:center;justify-content:center;position:relative}
.step-icon i{width:90px;height:90px;border-radius:50%;background:linear-gradient(150deg,#dce9f8,#f6e3d2)}
.step h3{font-size:17px;font-weight:500;margin-top:24px}
.step p{font-size:13.5px;line-height:22px;margin:12px auto 0;width:250px}

/* jobs */
.jobs{top:1830px;height:910px;background:linear-gradient(180deg,#f1f2f4 0%,#e9eaed 60%,#dfe1e5 100%)}
.job-card{position:absolute;width:290px;height:245px;background:#fff;border:1px solid #e1e4e8;border-radius:3px;overflow:hidden}
.job-card .flag{position:absolute;left:0;top:0;width:0;height:0;border-top:32px solid var(--orange);border-right:32px solid transparent}
.job-logo{position:absolute;left:20px;top:26px;width:70px;height:70px;border-radius:10px}
.job-card h3{position:absolute;left:20px;top:118px;font-size:17px;font-weight:500}
.job-card .summary{position:absolute;left:20px;top:150px;font-size:12px;display:flex;gap:8px;align-items:center}
.sq{width:10px;height:10px;background:var(--blue)}
.job-card .foot{position:absolute;left:0;right:0;bottom:0;height:56px;border-top:1px solid #eceef1;display:flex;align-items:center;justify-content:space-between;padding:0 18px;font-size:12px}
.loc{display:flex;gap:6px;align-items:center}
.apply{border:1px solid var(--blue);color:var(--blue);border-radius:12px;padding:3px 12px;font-size:11.5px;font-weight:600}
.btn-dark-outline{position:absolute;left:488px;top:780px;width:224px;text-align:center;border:2px solid var(--ink);padding:10px 0;font-size:13px;font-weight:500;color:var(--ink);background:rgba(255,255,255,.5)}

/* subscription */
.subscribe{top:2740px;height:660px;background:linear-gradient(90deg,#e9ecf2,#d5dce9)}
.sub-photo{position:absolute;left:135px;top:50px;width:445px;height:610px;background:linear-gradient(180deg,#cbd6e6,#8fa9cf 60%,#dfe6f1);border-radius:0}
.sub-form{position:absolute;left:627px;top:102px;width:423px}
.sub-form h2{font-size:34px;font-weight:700;text-transform:uppercase;margin-bottom:38px}
.sub-form h2 span{font-weight:400;color:var(--blue)}
.field{height:40px;background:#fff;border:1px solid #c8cfda;margin-bottom:16px;padding:0 12px;display:flex;align-items:center;justify-content:space-between;font-size:13px;color:#6a707b}
.upload{background:#e3e6eb;border:1px solid #c3c8d0;padding:3px 14px;color:var(--ink);font-size:12.5px}
.sub-form .btn-solid{margin-top:14px;padding:13px 52px;font-size:14px}

/* customers */
.customers{top:3400px;height:492px}
.client{position:absolute;width:168px;height:76px;border:1px solid #dfe2e6;display:flex;align-items:center;justify-content:center;font-family:"Poppins",Arial,sans-serif;font-weight:600;font-size:21px;color:#8c929b}
.chev{position:absolute;top:272px}

/* blog */
.blog{top:3892px;height:661px;background:linear-gradient(180deg,#1c6ec9,#0f55a8)}
.blog .section-title{color:#fff}
.blog .section-rule{background:#fff}
.post{position:absolute;top:203px;width:290px;height:356px;background:#fff}
.post-photo{height:178px}
.date{position:absolute;left:10px;top:0;width:54px;height:54px;background:var(--blue);color:#fff;font-size:12px;line-height:16px;text-align:center;padding-top:10px;font-weight:600}
.post h3{font-size:18px;font-weight:500;line-height:24px;margin:18px 16px 10px;color:var(--ink)}
.post p{font-size:12.5px;line-height:19px;margin:0 16px}

/* footer */
footer{top:4553px;height:347px;background:#fff}
.foot-brand{position:absolute;left:142px;top:60px;font-family:"Poppins",Arial,sans-serif;font-weight:600;font-size:25px;letter-spacing:6px;color:var(--ink)}
.foot-about{position:absolute;left:142px;top:115px;width:290px;font-size:12.5px;line-height:21px}
.foot-col{position:absolute;top:62px}
.foot-col h4{font-size:15px;font-weight:600;text-transform:uppercase;margin-bottom:22px}
.foot-col h4 span{color:var(--blue)}
.news{left:519px;width:280px}
.news p{font-size:12.5px;line-height:20px}
.news .input{height:34px;border:1px solid #c8cfda;border-radius:17px;margin-top:14px;padding:0 14px;display:flex;align-items:center;font-size:11.5px;color:#8a919c}
.news .btn-solid{margin-top:14px;border-radius:17px;padding:8px 22px;font-size:12px}
.contact-col{left:851px;width:220px}
.c-item{display:flex;gap:12px;font-size:12.5px;line-height:19px;margin-bottom:14px}
.c-item svg{flex:none;margin-top:2px}
.bottom{position:absolute;top:4900px;left:0;width:1200px;height:185px;border-top:1px solid #e4e6ea;text-align:center}
.bottom p{margin-top:60px;font-size:13px;color:var(--text)}
.bottom .social{display:flex;gap:8px;justify-content:center;margin-top:28px}
.bottom .dot{width:28px;height:28px;border-color:#3a3f47}
</style>
</head>
<body>

<div class="topbar">
  <div class="contact">
    <span><svg width="12" height="12" viewBox="0 0 24 24"><path fill="#fff" d="M6.6 10.8a15 15 0 0 0 6.6 6.6l2.2-2.2a1 1 0 0 1 1-.25 11 11 0 0 0 3.6.6 1 1 0 0 1 1 1V20a1 1 0 0 1-1 1A17 17 0 0 1 3 4a1 1 0 0 1 1-1h3.5a1 1 0 0 1 1 1c0 1.25.2 2.45.6 3.6a1 1 0 0 1-.25 1z"/></svg>555 0100 2200</span>
    <span><svg width="13" height="10" viewBox="0 0 26 20"><rect x="1" y="1" width="24" height="18" fill="none" stroke="#fff" stroke-width="2"/><path d="M1 1l12 10L25 1" fill="none" stroke="#fff" stroke-width="2"/></svg>info@brighthire.example</span>
  </div>
  <div class="social"><i class="dot"></i><i class="dot"></i><i class="dot"></i></div>
</div>

<header>
  <div class="brand">BRIGHTHIRE</div>
  <nav><span>How we work</span><span>Joblisting</span><span>Our customers</span><span>Blog</span><span>Contact</span></nav>
</header>

<section class="hero">
  <div class="hero-photo" role="img" aria-label="Hand placing a wooden block with a person icon on top of a pyramid of blocks"></div>
  <h1 class="hero-title">BRIGHTHIRE</h1>
  <p class="hero-text">Sed ut perspiciatis unde omnis iste natus error sit voluptatem accusantium doloremque laudantium, totam rem aperiam, eaque ipsa quae ab illo inventore veritatis</p>
  <span class="btn btn-solid">Get more info</span>
  <div class="arrow" style="left:60px;top:250px"><svg width="12" height="12" viewBox="0 0 12 12"><path d="M8 1L3 6l5 5" fill="none" stroke="#fff" stroke-width="2"/></svg></div>
  <div class="arrow" style="right:60px;top:250px"><svg width="12" height="12" viewBox="0 0 12 12"><path d="M4 1l5 5-5 5" fill="none" stroke="#fff" stroke-width="2"/></svg></div>
</section>

<section class="welcome">
  <div class="welcome-photo" role="img" aria-label="Recruitment concept: tablet with a network of candidate profiles"></div>
  <div class="welcome-copy">
    <div class="eyebrow">Welcome to</div>
    <h2>BRIGHTHIRE</h2>
    <div class="rule"></div>
    <p>Sed ut perspiciatis unde omnis iste natus error sit voluptatem accusantium doloremque laudantium, totam rem aperiam, eaque ipsa quae ab illo inventore veritatis et quasi architecto beatae vitae dicta sunt explicabo. Nemo enim ipsam voluptatem quia voluptas sit aspernatur aut odit aut fugit, sed</p>
    <span class="btn btn-outline">Read more</span>
  </div>
</section>

<section class="how">
  <h2 class="section-title" style="top:83px">How we <span>work</span></h2>
  <div class="section-rule" style="top:160px"></div>
  <div class="steps-line"></div>
  <div class="step" style="left:118px">
    <div class="step-icon"><i role="img" aria-label="Illustration of a person at a desk"></i></div>
    <h3>Register an account</h3>
    <p>Post a job to tell us about your project. We'll quickly match you with the right freelancers</p>
  </div>
  <div class="step" style="left:450px">
    <div class="step-icon"><i role="img" aria-label="Illustration of a magnifier over a team"></i></div>
    <h3>Specify &amp; search your job</h3>
    <p>Browse profiles, reviews, and proposals then interview top candidates.</p>
  </div>
  <div class="step" style="left:775px">
    <div class="step-icon"><i role="img" aria-label="Illustration of a signed document"></i></div>
    <h3>Apply for job</h3>
    <p>Use the Workly platform to chat, share files, and collaborate from your desktop or on the go.</p>
  </div>
</section>

<section class="jobs">
  <h2 class="section-title" style="top:70px">Job <span>listing</span></h2>
  <div class="section-rule" style="top:147px"></div>

  <div class="job-card" style="left:142px;top:190px"><i class="flag"></i><div class="job-logo" role="img" aria-label="Company emblem" style="background:linear-gradient(135deg,#e84c6c,#3b7bd8)"></div><h3>Developers</h3><div class="summary"><i class="sq"></i>Quis autem vel eum iure rep</div><div class="foot"><span class="loc"><svg width="10" height="13" viewBox="0 0 10 14"><path d="M5 0a5 5 0 0 0-5 5c0 4 5 9 5 9s5-5 5-9a5 5 0 0 0-5-5zm0 7a2 2 0 1 1 0-4 2 2 0 0 1 0 4z" fill="#1466c0"/></svg>South, Australia</span><span class="apply">Apply Now</span></div></div>
  <div class="job-card" style="left:458px;top:190px"><div class="job-logo" role="img" aria-label="Company emblem" style="background:linear-gradient(135deg,#8e44ad,#f39c12)"></div><h3>Scrum Master</h3><div class="summary"><i class="sq"></i>Quis autem vel eum iure rep</div><div class="foot"><span class="loc"><svg width="10" height="13" viewBox="0 0 10 14"><path d="M5 0a5 5 0 0 0-5 5c0 4 5 9 5 9s5-5 5-9a5 5 0 0 0-5-5zm0 7a2 2 0 1 1 0-4 2 2 0 0 1 0 4z" fill="#1466c0"/></svg>South, Australia</span><span class="apply">Apply Now</span></div></div>
  <div class="job-card" style="left:766px;top:190px"><i class="flag"></i><div class="job-logo" role="img" aria-label="Company emblem" style="background:linear-gradient(135deg,#1eaa9a,#6fd3c6)"></div><h3>Project Managers</h3><div class="summary"><i class="sq"></i>Quis autem vel eum iure rep</div><div class="foot"><span class="loc"><svg width="10" height="13" viewBox="0 0 10 14"><path d="M5 0a5 5 0 0 0-5 5c0 4 5 9 5 9s5-5 5-9a5 5 0 0 0-5-5zm0 7a2 2 0 1 1 0-4 2 2 0 0 1 0 4z" fill="#1466c0"/></svg>South, Australia</span><span class="apply">Apply Now</span></div></div>

  <div class="job-card" style="left:142px;top:472px"><div class="job-logo" role="img" aria-label="Company emblem" style="background:linear-gradient(135deg,#2a6fd6,#7bc043)"></div><h3>Project Designers</h3><div class="summary"><i class="sq"></i>Quis autem vel eum iure rep</div><div class="foot"><span class="loc"><svg width="10" height="13" viewBox="0 0 10 14"><path d="M5 0a5 5 0 0 0-5 5c0 4 5 9 5 9s5-5 5-9a5 5 0 0 0-5-5zm0 7a2 2 0 1 1 0-4 2 2 0 0 1 0 4z" fill="#1466c0"/></svg>South, Australia</span><span class="apply">Apply Now</span></div></div>
  <div class="job-card" style="left:458px;top:472px"><i class="flag"></i><div class="job-logo" role="img" aria-label="Company emblem" style="background:linear-gradient(135deg,#3a9d4a,#9bd17c)"></div><h3>Project Managers</h3><div class="summary"><i class="sq"></i>Quis autem vel eum iure rep</div><div class="foot"><span class="loc"><svg width="10" height="13" viewBox="0 0 10 14"><path d="M5 0a5 5 0 0 0-5 5c0 4 5 9 5 9s5-5 5-9a5 5 0 0 0-5-5zm0 7a2 2 0 1 1 0-4 2 2 0 0 1 0 4z" fill="#1466c0"/></svg>South, Australia</span><span class="apply">Apply Now</span></div></div>
  <div class="job-card" style="left:766px;top:472px"><div class="job-logo" role="img" aria-label="Company emblem" style="background:linear-gradient(135deg,#2bb3c0,#2a6fd6)"></div><h3>Developers</h3><div class="summary"><i class="sq"></i>Quis autem vel eum iure rep</div><div class="foot"><span class="loc"><svg width="10" height="13" viewBox="0 0 10 14"><path d="M5 0a5 5 0 0 0-5 5c0 4 5 9 5 9s5-5 5-9a5 5 0 0 0-5-5zm0 7a2 2 0 1 1 0-4 2 2 0 0 1 0 4z" fill="#1466c0"/></svg>South, Australia</span><span class="apply">Apply Now</span></div></div>

  <span class="btn-dark-outline heading">VIEW MORE JOB LISTING</span>
</section>

<section class="subscribe">
  <div class="sub-photo" role="img" aria-label="Smiling candidate holding a laptop"></div>
  <div class="sub-form">
    <h2>Subscription <span>forms</span></h2>
    <div class="field">Name</div>
    <div class="field">Surname</div>
    <div class="field">Email address</div>
    <div class="field">Phone number</div>
    <div class="field">Upload your resume <span class="upload">Upload</span></div>
    <span class="btn btn-solid">Subscription</span>
  </div>
</section>

<section class="customers">
  <h2 class="section-title" style="top:80px;font-weight:700">Our <span>customers</span></h2>
  <div class="section-rule" style="top:157px"></div>
  <svg class="chev" style="left:92px" width="14" height="24" viewBox="0 0 14 24"><path d="M12 2L3 12l9 10" fill="none" stroke="#9aa0a8" stroke-width="2"/></svg>
  <svg class="chev" style="right:92px" width="14" height="24" viewBox="0 0 14 24"><path d="M2 2l9 10-9 10" fill="none" stroke="#9aa0a8" stroke-width="2"/></svg>
  <div class="client" style="left:142px;top:214px">Nimbly</div>
  <div class="client" style="left:324px;top:214px">Castwave</div>
  <div class="client" style="left:506px;top:214px">Ortholux</div>
  <div class="client" style="left:688px;top:214px">Veltrix</div>
  <div class="client" style="left:870px;top:214px">Quarrel</div>
  <div class="client" style="left:142px;top:309px">Loomhaus</div>
  <div class="client" style="left:324px;top:309px">Pennant</div>
  <div class="client" style="left:506px;top:309px">Arbora</div>
  <div class="client" style="left:688px;top:309px">Tidewell</div>
  <div class="client" style="left:870px;top:309px">Fernbrook</div>
</section>

<section class="blog">
  <h2 class="section-title" style="top:82px">Latest blog</h2>
  <div class="section-rule" style="top:158px"></div>
  <article class="post" style="left:142px"><div class="post-photo" role="img" aria-label="Hand touching a digital network of people" style="background:linear-gradient(135deg,#9fb0c4,#4d6580)"></div><div class="date">Oct 01<br>2019</div><h3>Sed ut perspiciatis unde omnis iste natus</h3><p>Sed ut perspiciatis unde omnis iste natus error sit voluptatem accusantium doloque latum, totam rem aperiam</p></article>
  <article class="post" style="left:458px"><div class="post-photo" role="img" aria-label="Business handshake across a desk" style="background:linear-gradient(135deg,#e6e2dc,#8b9cb3)"></div><div class="date">Oct 01<br>2019</div><h3>Sed ut perspiciatis unde omnis iste natus</h3><p>Sed ut perspiciatis unde omnis iste natus error sit voluptatem accusantium doloque latum, totam rem aperiam</p></article>
  <article class="post" style="left:766px"><div class="post-photo" role="img" aria-label="Interlocking gears on a dark background" style="background:linear-gradient(135deg,#3b3f46,#8d9199)"></div><div class="date">Oct 01<br>2019</div><h3>Sed ut perspiciatis unde omnis iste natus</h3><p>Sed ut perspiciatis unde omnis iste natus error sit voluptatem accusantium doloque latum, totam rem aperiam</p></article>
</section>

<footer>
  <div class="foot-brand">BRIGHTHIRE</div>
  <p class="foot-about">Sed ut perspiciatis unde omnis iste natus error sit voluptatem accusantium doloremque latium. totam rem aperiam, eaque ipsa quae ab illo inve veritatis et quasi architecto beatae vitae dicta sunt explicabo. Nemo enim ipsam voluptatem quia voluptas sit aspernatur</p>
  <div class="foot-col news">
    <h4>Sign up for <span>newsletter</span></h4>
    <p>excepteur sint occaecat cupidatat non proident, sunt in culpa qui officia deserunt</p>
    <div class="input">Enter email</div>
    <span class="btn btn-solid">Subscribe</span>
  </div>
  <div class="foot-col contact-col">
    <h4>Contact <span>us</span></h4>
    <div class="c-item"><svg width="12" height="16" viewBox="0 0 10 14"><path d="M5 0a5 5 0 0 0-5 5c0 4 5 9 5 9s5-5 5-9a5 5 0 0 0-5-5zm0 7a2 2 0 1 1 0-4 2 2 0 0 1 0 4z" fill="#1466c0"/></svg><span>BrightHire 12/8 Harbour Lane, 20 04 Portvale</span></div>
    <div class="c-item"><svg width="14" height="14" viewBox="0 0 24 24"><path fill="#1466c0" d="M6.6 10.8a15 15 0 0 0 6.6 6.6l2.2-2.2a1 1 0 0 1 1-.25 11 11 0 0 0 3.6.6 1 1 0 0 1 1 1V20a1 1 0 0 1-1 1A17 17 0 0 1 3 4a1 1 0 0 1 1-1h3.5a1 1 0 0 1 1 1c0 1.25.2 2.45.6 3.6a1 1 0 0 1-.25 1z"/></svg><span>Phone:<br>08 5550 1290</span></div>
    <div class="c-item"><svg width="14" height="11" viewBox="0 0 26 20"><rect x="1" y="1" width="24" height="18" fill="#1466c0"/><path d="M1 1l12 10L25 1" fill="none" stroke="#fff" stroke-width="2"/></svg><span>Email:<br>hello@brighthire.example</span></div>
  </div>
</footer>

<div class="bottom">
  <p>BrightHire © 2019 All Rights Reserved | Privacy Policy | Terms and Conditions</p>
  <div class="social"><i class="dot"></i><i class="dot"></i><i class="dot"></i><i class="dot"></i></div>
</div>

</body>
</html>
```